Wordpress theme website for professionals working together

My partner and I are offering business services, my wife in the energy business as mainly as member of the board of commissioners. I am working as interim manager/consultant in the accounting and finance area. Both activities are connected in one company VELMOT BV (dutch ltd). We need a CV based website. Beside this we do some financial and accounting services.

Target Market(s)

small medium business

Font styles to use
Sans Serif

Colors

Designer to choose colors to be used in the design.

Requirements
Must have
• Pictures of both members.
• CLEAN AND SIMPLE
• I LIKE BLACK & WHITE
Nice to have
• I like design like this theme: http://theme.pruxelo-example.com/resume/

```html
<!DOCTYPE html>
<html lang="en">
<head>
<meta charset="utf-8">
<title>VELMOT BV – Resume</title>
<link href="https://fonts.googleapis.com/css2?family=Lato:wght@400;700;900&display=swap" rel="stylesheet">
<style>
:root{
  --ink:#111111;
  --dark:#222222;
  --text:#333333;
  --muted:#555555;
  --brand:#1d3a6e;
  --accent:#c8161d;
  --light:#f1f1f1;
  --track:#e6e6e6;
  --line:#cfcfcf;
  --white:#ffffff;
}
*{box-sizing:border-box;margin:0;padding:0}
html,body{width:1200px;height:3114px;overflow:hidden;background:var(--white)}
body{font-family:'Lato',Arial,sans-serif;color:var(--text);position:relative}
.abs{position:absolute}

/* header */
.site-header{position:absolute;left:0;top:0;width:1200px;height:105px;background:var(--white)}
.brand{position:absolute;left:75px;top:34px;font-size:34px;font-weight:900;color:var(--brand);letter-spacing:.5px}
.main-nav{position:absolute;right:75px;top:56px;display:flex;gap:34px;font-size:14px;color:var(--ink);letter-spacing:.3px}
.main-nav .active{font-weight:700}

/* hero */
.hero{position:absolute;left:0;top:105px;width:1200px;height:492px;background:linear-gradient(90deg,#c7cbd3 0%,#d3d6dc 45%,#c9ccd2 100%)}
.hero-photo{position:absolute;left:520px;top:0;width:680px;height:492px;background:linear-gradient(90deg,rgba(205,208,214,0) 0%,#a8a9ad 25%,#8a7f78 55%,#3b3f4a 100%)}
.hero-name{position:absolute;left:82px;top:98px;font-size:52px;font-weight:400;color:var(--ink)}
.hero-sub{position:absolute;left:85px;top:172px;font-size:20px;color:var(--ink)}
.hero-text{position:absolute;left:85px;top:208px;width:450px;font-size:14.5px;line-height:23px;color:var(--muted)}
.partner-avatar{position:absolute;left:75px;top:355px;width:96px;height:96px;border-radius:50%;background:var(--dark)}
.partner-name{position:absolute;left:197px;top:368px;font-size:19px;font-weight:700;color:var(--ink)}
.partner-btn{position:absolute;left:197px;top:403px;width:116px;height:42px;background:var(--white);font-size:15px;color:var(--ink);display:flex;align-items:center;justify-content:center}

/* section title */
.section-title{position:absolute;left:0;width:1200px;text-align:center;font-size:32px;font-weight:900;color:var(--ink);letter-spacing:.5px}

/* skills */
.skill{position:absolute;left:0;width:1200px;height:20px;font-size:14.5px;color:var(--ink)}
.skill-label{position:absolute;right:705px;top:0;white-space:nowrap}
.skill-track{position:absolute;left:525px;top:4px;width:360px;height:14px;background:var(--track)}
.skill-fill{height:14px;background:var(--dark)}
.skill-value{position:absolute;left:906px;top:0}

/* jobs */
.jobs-current{position:absolute;left:0;top:1075px;width:600px;height:531px;background:var(--dark);color:var(--white)}
.jobs-finished{position:absolute;left:600px;top:1075px;width:600px;height:531px;background:var(--light);color:var(--ink)}
.jobs-title{position:absolute;font-size:32px;font-weight:900}
.job{position:absolute;width:310px}
.job h3{font-size:20px;font-weight:700;margin-bottom:14px}
.job p{font-size:14.5px;line-height:23px}

/* education */
.edu{position:absolute;width:310px;text-align:center}
.edu h3{font-size:20px;font-weight:400;color:var(--ink);margin-bottom:14px}
.edu p{font-size:14.5px;line-height:23px;color:var(--muted)}

/* worked for */
.worked{position:absolute;left:0;top:1841px;width:1200px;height:277px;background:var(--light)}
.client{position:absolute;font-size:34px;font-weight:400;color:var(--dark)}

/* other */
.other-photo{position:absolute;left:254px;top:2237px;width:334px;height:209px;background:linear-gradient(135deg,#c9b6a2 0%,#a89581 45%,#7f8fa6 100%)}
.other-text{position:absolute;left:614px;top:2250px;width:340px}
.other-text h3{font-size:20px;font-weight:700;color:var(--ink);margin-bottom:12px}
.other-text p{font-size:14.5px;line-height:23px;color:var(--muted)}

/* contact */
.contact{position:absolute;left:0;top:2522px;width:1200px;height:402px;background:var(--light)}
.field{position:absolute;background:var(--white);border:1px solid var(--line);font-size:13px;color:var(--ink);padding:12px 14px}
.submit{position:absolute;left:497px;top:304px;width:207px;height:49px;background:var(--dark);color:var(--white);font-size:17px;font-weight:700;display:flex;align-items:center;justify-content:center;letter-spacing:.5px}

/* footer */
.footer-nav{position:absolute;left:0;top:2973px;width:1200px;display:flex;justify-content:center;gap:34px;font-size:13.5px;color:var(--ink)}
.copyright{position:absolute;left:0;top:3011px;width:1200px;text-align:center;font-size:12px;color:var(--muted)}
.social{position:absolute;left:508px;top:3045px;display:flex;gap:24px}
.social span{width:18px;height:18px;border-radius:50%;background:var(--muted);display:block}
</style>
</head>
<body>

<header class="site-header">
  <div class="brand">VELMOT BV</div>
  <nav class="main-nav">
    <span class="active">HOME</span><span>ACTUAL JOBS</span><span>FINISHED JOBS</span><span>SKILLS</span><span>EDUCATION</span><span>CONTACT</span><span>MORE...</span>
  </nav>
</header>

<section class="hero">
  <div class="hero-photo" role="img" aria-label="Portrait photo of Marit outdoors in winter"></div>
  <h1 class="hero-name">Marit</h1>
  <h2 class="hero-sub">About me</h2>
  <p class="hero-text">Nullam condimentum faucibus consequat. Aenean quis leo felis. Morbi hendrerit auctor purus, sed malesuada tortor. Lorem ipsum dolor sit amet, consectetur adipiscing elit. Donec ullamcorper, leo eu sollicitudin malesuada, nibh nunc condimentum lectus..</p>
  <div class="partner-avatar" role="img" aria-label="Portrait photo of Joost"></div>
  <div class="partner-name">Joost</div>
  <div class="partner-btn">Click Here</div>
</section>

<h2 class="section-title" style="top:625px">SKILLS</h2>
<div class="skill" style="top:717px"><span class="skill-label">General management</span><div class="skill-track"><div class="skill-fill" style="width:61%"></div></div><span class="skill-value">65%</span></div>
<div class="skill" style="top:759px"><span class="skill-label">Energy knowledge</span><div class="skill-track"><div class="skill-fill" style="width:42%"></div></div><span class="skill-value">40%</span></div>
<div class="skill" style="top:800px"><span class="skill-label">Gas knowledge</span><div class="skill-track"><div class="skill-fill" style="width:96%"></div></div><span class="skill-value">98%</span></div>
<div class="skill" style="top:842px"><span class="skill-label">People management</span><div class="skill-track"><div class="skill-fill" style="width:76%"></div></div><span class="skill-value">88%</span></div>
<div class="skill" style="top:883px"><span class="skill-label">Project management</span><div class="skill-track"><div class="skill-fill" style="width:71%"></div></div><span class="skill-value">70%</span></div>
<div class="skill" style="top:925px"><span class="skill-label">Team player</span><div class="skill-track"><div class="skill-fill" style="width:100%"></div></div><span class="skill-value">100%</span></div>
<div class="skill" style="top:966px"><span class="skill-label">Trouble shooter</span><div class="skill-track"><div class="skill-fill" style="width:79%"></div></div><span class="skill-value">89%</span></div>
<div class="skill" style="top:1008px"><span class="skill-label">ETC.</span><div class="skill-track"><div class="skill-fill" style="width:22%"></div></div><span class="skill-value">15%</span></div>

<section class="jobs-current">
  <h2 class="jobs-title" style="left:137px;top:57px">ACTUAL JOBS</h2>
  <div class="job" style="left:139px;top:120px"><h3>Director Veldgas</h3><p>Nullam condimentum faucibus consequat. Aenean quis leo felis. Morbi hendrerit auctor purus, sed malesuada tortor...</p></div>
  <div class="job" style="left:139px;top:250px"><h3>Netwerk Oost</h3><p>Nullam condimentum faucibus consequat. Aenean quis leo felis. Morbi hendrerit auctor purus, sed malesuada tortor...</p></div>
</section>
<section class="jobs-finished">
  <h2 class="jobs-title" style="left:79px;top:57px">FINISHED JOBS</h2>
  <div class="job" style="left:76px;top:118px"><h3>Director Gasnoord</h3><p>Nullam condimentum faucibus consequat. Aenean quis leo felis. Morbi hendrerit auctor purus, sed malesuada tortor...</p></div>
  <div class="job" style="left:76px;top:244px"><h3>Advisor Gas</h3><p>Nullam condimentum faucibus consequat. Aenean quis leo felis. Morbi hendrerit auctor purus, sed malesuada tortor...</p></div>
  <div class="job" style="left:76px;top:370px"><h3>Oipoip o kkljk</h3><p>Nullam condimentum faucibus consequat. Aenean quis leo felis. Morbi hendrerit auctor purus, sed malesuada tortor...</p></div>
</section>

<h2 class="section-title" style="top:1634px">EDUCATION</h2>
<div class="edu" style="left:266px;top:1704px"><h3>NSU</h3><p>Nullam condimentum faucibus consequat. Aenean quis leo felis. Morbi hendrerit auctor purus, sed malesuada tortor...</p></div>
<div class="edu" style="left:617px;top:1704px"><h3>Lyceum Noord</h3><p>Nullam condimentum faucibus consequat. Aenean quis leo felis. Morbi hendrerit auctor purus, sed malesuada tortor...</p></div>

<section class="worked">
  <h2 class="section-title" style="top:38px">WORKED FOR</h2>
  <div class="client" style="left:398px;top:122px">Gasnoord</div>
  <div class="client" style="left:672px;top:122px">The Loom Company</div>
</section>

<h2 class="section-title" style="top:2164px">OTHER</h2>
<div class="other-photo" role="img" aria-label="Photo of a person reading a book outdoors"></div>
<div class="other-text">
  <h3>Reading</h3>
  <p>Nullam condimentum faucibus consequat. Aenean quis leo felis. Morbi hendrerit auctor purus, sed malesuada tortor. Lorem ipsum dolor sit amet, consectetur adipiscing elit. Donec ullamcorper, leo eu sollicitudin malesuada, nibh nunc condimentum lectus.</p>
</div>

<section class="contact">
  <h2 class="section-title" style="top:38px">CONTACT US</h2>
  <div class="field" style="left:254px;top:114px;width:333px;height:41px">Name</div>
  <div class="field" style="left:614px;top:114px;width:333px;height:41px">Email Address</div>
  <div class="field" style="left:254px;top:164px;width:693px;height:122px">Message</div>
  <div class="submit">SUBMIT</div>
</section>

<footer>
  <nav class="footer-nav"><span>HOME</span><span>ACTUAL JOBS</span><span>FINISHED JOBS</span><span>SKILLS</span><span>EDUCATION</span><span>CONTACT</span><span>MORE...</span></nav>
  <p class="copyright">Copyright© 2018 Company Name. All Right Reserved</p>
  <div class="social" aria-label="Social links"><span></span><span></span><span></span><span></span><span></span></div>
</footer>

</body>
</html>
```